Elegant and modern Wedding Photography brochure

My existing brochure (attached) needs a major facelift. This is one of the main selling tools - it gets emailed to my clients when they make an equiry on what packages i offer and it is printed out and walked through at our first meeting. This brochure is as critical as my website - it needs to sing!

I'm looking for an eye-catching design that says:
Elegant
Modern
Clean
Crisp
Not cutesy or lovey-dovey thanks - we are more sophisticated and professional than that.

Update images to some of the latest weddings I've shot also. Let me know files and resolution you need. I've enabled right-click to download images on my site for a limited time. Please note that I retain copyright and will pursue any breeches.

Http://www.sarahkelbrin.com/Melbourne-wedding-photography
Updates

Thanks for all of your designs! Will take a few days to decide.

Target Market(s)

Australian Women aged 24-44

Industry/Entity Type

Wedding

Font styles to use
Other font styles liked:
• Century Gothic

Requirements
Must have
• Easy to print - does not have to be 6 A4 pages like the existing brochure
Nice to have
• Some full page images - The photos are supposed to be the hero here :-)
Should not have
• Not cutesy or lovey-dovey thanks - we are more sophisticated and professional than that.

No black backgrounds, I prefer a white thanks

No images in organic shaped boxes (like the rectangles in the logo - no thanks).
Keep the lines straight and sharp

```html
<!DOCTYPE html>
<html lang="en">
<head>
<meta charset="utf-8">
<title>Claire's approach – Wedding Photography Brochure, Page 2</title>
<link rel="stylesheet" href="https://fonts.googleapis.com/css2?family=Montserrat:wght@700&family=Questrial&display=swap">
<style>
  :root {
    --plum: #8a2c8c;
    --plum-dark: #6e1f70;
    --ink: #7a7a7a;
    --paper: #ffffff;
    --photo-sky: #c9d3c6;
    --photo-field: #a8a477;
    --photo-warm: #8a7452;
  }
  * { box-sizing: border-box; margin: 0; padding: 0; }
  html, body { width: 849px; height: 1200px; overflow: hidden; background: var(--paper); }
  .page {
    position: relative;
    width: 849px;
    height: 1200px;
    overflow: hidden;
    background: var(--paper);
    font-family: "Questrial", "Century Gothic", sans-serif;
    color: var(--ink);
  }
  .side-band {
    position: absolute;
    left: 0; top: 0;
    width: 70px; height: 1200px;
    background: var(--plum);
  }
  .page-number {
    position: absolute;
    left: 20px; bottom: 22px;
    color: var(--paper);
    font-size: 24px;
  }
  .hero-photo {
    position: absolute;
    left: 70px; top: 0;
    width: 779px; height: 570px;
    background:
      linear-gradient(to bottom, rgba(255,255,255,0) 72%, var(--paper) 100%),
      radial-gradient(ellipse 40% 75% at 32% 40%, #efeae4 0%, rgba(239,234,228,0) 70%),
      linear-gradient(to bottom, var(--photo-sky) 0%, #b9c2a8 35%, var(--photo-field) 60%, var(--photo-warm) 85%);
  }
  .hero-title {
    position: absolute;
    right: 34px; top: 478px;
    text-align: right;
    color: var(--paper);
    font-family: "Montserrat", "Century Gothic", sans-serif;
    font-weight: 700;
    text-shadow: 0 1px 3px rgba(80,60,40,0.35);
  }
  .hero-title h1 { font-size: 42px; letter-spacing: 0.3px; line-height: 1.1; }
  .hero-title p { font-size: 23px; margin-top: 2px; }
  .content {
    position: absolute;
    left: 192px; top: 574px;
    width: 580px;
    display: grid;
    grid-template-columns: 258px 258px;
    column-gap: 64px;
  }
  .section { margin-bottom: 30px; }
  .section h2 {
    font-family: "Montserrat", "Century Gothic", sans-serif;
    font-weight: 700;
    font-size: 15px;
    color: var(--plum-dark);
    margin-bottom: 14px;
  }
  .section p {
    font-size: 15.5px;
    line-height: 18px;
    margin-bottom: 16px;
  }
</style>
</head>
<body>
  <main class="page">
    <div class="side-band"></div>
    <div class="hero-photo" role="img" aria-label="Wedding photo: bride and groom kissing beside railway tracks in a golden field"></div>
    <header class="hero-title">
      <h1>Claire's approach…</h1>
      <p>Enjoy your special day!</p>
    </header>

    <section class="content">
      <div class="column">
        <article class="section">
          <h2>Style &amp; Approach</h2>
          <p>Claire can observe and capture your wedding day in the background, quietly and quickly taking photojournalistic pictures rather than directing it if you prefer. Or she can confidently play the role of Art Director and instruct beautiful poses. Either way, what's most important is that her clients are relaxed and having a really great time on their wedding day.</p>
        </article>
        <article class="section">
          <h2>Formal Photography</h2>
          <p>Many of Claire's clients book her because of the easy-going approach she has. They can get on with having a great time on their day without worrying about formal photography. However, there are occasions when clients do want formal family pictures, and Claire is more than happy to accommodate their requests.</p>
          <p>In order to keep the disruption on the day to a minimum, we recommend that Claire photographs no more than 6 groups, and a select number of the special couple.</p>
        </article>
      </div>
      <div class="column">
        <article class="section">
          <h2>Image Presentation</h2>
          <p>The most professional way of presenting clients with their photographs is in an elegantly designed photo book. Claire's clients only pay one fixed price for the photography, regardless of how many images taken. There are no hard sell procedures to go through, and the completed book is prepared within 2-6 weeks after the wedding day.</p>
        </article>
        <article class="section">
          <h2>Time of Year</h2>
          <p>Signature pictures can be taken on overcast days or winter months. Don't worry if the sky is not perfectly blue. In the end, regardless of the weather – it's the timeless mood of the day that Claire strives to capture.</p>
        </article>
      </div>
    </section>

    <div class="page-number">2</div>
  </main>
</body>
</html>
```